Accounting firm needing business card / letterhead designed
Marcus L. Trenholm, CPA
marcus@veltrowledger.com
www.veltrowledger.com
842 E Alder Ave Maplecrest, IN 43827
555-562-0974

```html
<!DOCTYPE html>
<html lang="en">
<head>
<meta charset="utf-8">
<title>Veltro Ledger — Business Card</title>
<link href="https://fonts.googleapis.com/css2?family=Roboto:wght@400;700&family=Roboto+Condensed:wght@700&display=swap" rel="stylesheet">
<style>
  :root {
    --navy: #262262;
    --green: #8dc63f;
    --paper: #f4f4f4;
    --backdrop: #cfcfcf;
    --ink-grey: #4a4a4a;
    --rule: #b8b8b8;
  }
  * { box-sizing: border-box; margin: 0; padding: 0; }
  html, body { width: 1200px; height: 960px; overflow: hidden; }
  body {
    background: var(--backdrop);
    font-family: "Roboto", Arial, sans-serif;
    position: relative;
  }
  .card {
    position: absolute;
    width: 600px;
    height: 343px;
    border-radius: 18px;
    overflow: hidden;
  }
  .card-front {
    left: 322px; top: 106px;
    background: var(--navy);
    color: #fff;
    text-align: center;
  }
  .front-wordmark {
    position: absolute;
    left: 0; right: 0; top: 140px;
    font-weight: 700;
    font-size: 54px;
    line-height: 64px;
    letter-spacing: 3px;
    color: #fff;
  }
  .front-web {
    position: absolute;
    left: 0; right: 0; top: 283px;
    font-size: 14px;
    letter-spacing: 6.5px;
    color: #fff;
  }
  .card-back {
    left: 320px; top: 493px;
    background: var(--paper);
  }
  .back-swoosh { position: absolute; left: 0; top: 0; }
  .back-wordmark {
    position: absolute;
    left: 60px; width: 232px; top: 146px;
    text-align: center;
    font-weight: 700;
    font-size: 27px;
    letter-spacing: 1px;
    color: var(--navy);
  }
  .divider {
    position: absolute;
    left: 306px; top: 92px;
    width: 1px; height: 160px;
    background: var(--rule);
  }
  .contact { position: absolute; left: 331px; top: 98px; color: var(--ink-grey); }
  .contact-name {
    font-family: "Roboto Condensed", "Roboto", Arial, sans-serif;
    font-weight: 700;
    font-size: 21px;
    line-height: 24px;
    color: var(--navy);
    margin-bottom: 10px;
  }
  .contact-address { font-size: 14px; line-height: 18px; margin-bottom: 10px; }
  .contact-list { list-style: none; font-size: 14px; line-height: 19px; }
  .contact-list li { display: flex; align-items: center; gap: 9px; }
  .contact-list svg { width: 13px; height: 13px; fill: var(--navy); flex: none; }
</style>
</head>
<body>
  <section class="card card-front" aria-label="Card front">
    <div class="front-wordmark">VELTRO LEDGER</div>
    <div class="front-web">www.veltrowledger.com</div>
  </section>

  <section class="card card-back" aria-label="Card back">
    <svg class="back-swoosh" width="600" height="343" viewBox="0 0 600 343">
      <path d="M0 0 H10 Q30 230 68 343 H0 Z" fill="var(--navy)"/>
      <path d="M13 0 H17 Q44 220 90 343 H76 Q36 225 13 0 Z" fill="var(--green)"/>
    </svg>
    <div class="back-wordmark">VELTRO LEDGER</div>
    <div class="divider"></div>
    <div class="contact">
      <div class="contact-name">Marcus L. Trenholm, CPA</div>
      <div class="contact-address">842 E Alder Ave<br>Maplecrest, IN 43827</div>
      <ul class="contact-list">
        <li><svg viewBox="0 0 24 24"><path d="M6.6 10.8a15.1 15.1 0 0 0 6.6 6.6l2.2-2.2a1 1 0 0 1 1-.25 11.4 11.4 0 0 0 3.6.57 1 1 0 0 1 1 1V20a1 1 0 0 1-1 1A17 17 0 0 1 3 4a1 1 0 0 1 1-1h3.5a1 1 0 0 1 1 1c0 1.25.2 2.45.57 3.57a1 1 0 0 1-.25 1z"/></svg>555-562-0974</li>
        <li><svg viewBox="0 0 24 24"><path d="M2 6h20v12H2z"/><path d="M3 7l9 6 9-6" fill="none" stroke="#f4f4f4" stroke-width="2"/></svg>marcus@veltrowledger.com</li>
        <li><svg viewBox="0 0 24 24"><circle cx="12" cy="12" r="10"/><path d="M2 12h20M12 2c3 3 3 17 0 20M12 2c-3 3-3 17 0 20" fill="none" stroke="#f4f4f4" stroke-width="1.5"/></svg>www.veltrowledger.com</li>
      </ul>
    </div>
  </section>
</body>
</html>
```